Thornbury Building Company - Card Design

I am looking to use the logo designs that you already did for me to develop a business card. I would like the card to have a black background and be double sided. I want white and green logo and text. I have attached an inspiration photo of a look that I like. I would like to use the Vertical Logo attached to take up the full front side of the card. On the back where I have my name and information, I would like to have the horizontal logo or maybe even just the image of the 'A' and trees without the text. I am open, but I am looking for something clean and simple and I want the green to really pop! Additional files can be found under Design #: 58302946

Target Market(s)

Homeowners

Industry/Entity Type

Construction

Contact Information for Business Card

Name: Marcus Thornbury, Title: Project Manager, Phone: 555.274.8136, Email: thornburybuildingcompany@mailvesta.com, address: 487 Larkspur Ln, Maplecrest, QX 95033, Lic# 2468317

Colors
00AB8E
00BBA5
67D7C9
C6EFE9
E9F9F6

Requirements
Nice to have
• I would like to see the logos that I have already got from ArtLoomHub, though I am open to new ones

```html
<!DOCTYPE html>
<html lang="en">
<head>
<meta charset="utf-8">
<title>Thornbury Building Company – Business Card</title>
<link href="https://fonts.googleapis.com/css2?family=Open+Sans:wght@400;600;700&display=swap" rel="stylesheet">
<style>
  :root {
    --backdrop: #474747;
    --card: #161616;
    --green: #6ab544;
    --white: #ffffff;
  }
  * { box-sizing: border-box; margin: 0; padding: 0; }
  html, body {
    width: 1200px; height: 801px; overflow: hidden;
    background: var(--backdrop);
    font-family: "Open Sans", Arial, sans-serif;
  }
  .sheet {
    width: 1200px; height: 801px;
    display: flex; align-items: center; justify-content: center; gap: 40px;
  }
  .card {
    position: relative;
    width: 540px; height: 309px;
    background: var(--card);
    border: 2px solid var(--green);
    border-radius: 16px;
    overflow: hidden;
    color: var(--white);
  }

  /* Info side */
  .brand {
    position: absolute; left: 30px; top: 30px;
    display: flex; align-items: center; gap: 12px;
  }
  .brand-square { width: 26px; height: 26px; background: var(--green); flex: none; }
  .brand-name {
    font-weight: 700; font-size: 22px; letter-spacing: 0.5px;
    color: var(--white); text-transform: uppercase; white-space: nowrap;
  }
  .person { position: absolute; left: 30px; top: 96px; }
  .person-name { color: var(--green); font-weight: 700; font-size: 21px; line-height: 1.2; }
  .person-title { font-size: 14px; line-height: 1.4; }
  .contact { position: absolute; left: 30px; top: 160px; list-style: none; }
  .contact li {
    display: flex; align-items: center; gap: 8px;
    font-size: 13.5px; line-height: 21px; white-space: nowrap;
  }
  .contact svg { width: 12px; height: 12px; flex: none; fill: var(--green); }
  .license-band {
    position: absolute; left: 0; right: 0; bottom: 14px; height: 28px;
    background: var(--green);
    display: flex; align-items: center; padding-left: 30px;
    font-size: 13.5px; color: var(--white);
  }

  /* Logo side */
  .card-front { display: flex; align-items: center; justify-content: center; }
  .front-lockup { text-align: center; }
  .front-name {
    font-weight: 700; font-size: 30px; line-height: 1.15; letter-spacing: 1px;
    color: var(--white); text-transform: uppercase;
  }
  .established {
    margin-top: 16px;
    font-size: 12px; letter-spacing: 4px; color: var(--white);
  }
</style>
</head>
<body>
<main class="sheet">
  <section class="card card-back" aria-label="Contact side">
    <div class="brand">
      <span class="brand-square"></span>
      <span class="brand-name">Thornbury Building Company</span>
    </div>
    <div class="person">
      <p class="person-name">Marcus Thornbury</p>
      <p class="person-title">Project Manager</p>
    </div>
    <ul class="contact">
      <li>
        <svg viewBox="0 0 24 24" aria-hidden="true"><path d="M6.6 10.8a15 15 0 0 0 6.6 6.6l2.2-2.2c.3-.3.7-.4 1-.2 1.1.4 2.3.6 3.6.6.6 0 1 .4 1 1V20c0 .6-.4 1-1 1C10.6 21 3 13.4 3 4c0-.6.4-1 1-1h3.5c.6 0 1 .4 1 1 0 1.3.2 2.5.6 3.6.1.3 0 .7-.2 1z"/></svg>
        555.274.8136
      </li>
      <li>
        <svg viewBox="0 0 24 24" aria-hidden="true"><path d="M2 5h20v14H2z M2 5l10 8 10-8" fill="none" stroke="#6ab544" stroke-width="2.5"/></svg>
        thornburybuildingcompany@mailvesta.com
      </li>
      <li>
        <svg viewBox="0 0 24 24" aria-hidden="true"><path d="M12 2a7 7 0 0 0-7 7c0 5 7 13 7 13s7-8 7-13a7 7 0 0 0-7-7zm0 9.5a2.5 2.5 0 1 1 0-5 2.5 2.5 0 0 1 0 5z"/></svg>
        487 Larkspur Ln, Maplecrest, QX 95033
      </li>
    </ul>
    <div class="license-band">License# 2468317</div>
  </section>

  <section class="card card-front" aria-label="Logo side">
    <div class="front-lockup">
      <p class="front-name">Thornbury<br>Building Company</p>
      <p class="established">ESTD 2020</p>
    </div>
  </section>
</main>
</body>
</html>
```